Creative, fresh business card design for Ripplecraft Facades

We need a fresh, creative business card design for Ripplecraft Facades. We are the manufacturer of Ripplecraft Facades in Australia. Wall panels are 2400 x 1200mm panels made from MDF and feature 3D patterns on the face of the panel. The colours to be used are green, silver/grey and white RGB
Red 187
Green 207
Blue 65.

An idea is to possibly use a watermark of one of our designs as a background (like on the "Grids" design on the left hand side of page 2 of our brochure).

Target Market(s)

Interior designers, architects, builders and home renovators

Industry/Entity Type

Business

Contact Information for Business Card

Details to go on the card are:
Our logo (attached),
Slogan: "Decorative panels for interiors and exteriors",
Contact name,
Position,
Mobile phone number,
Business address,
Business phone,
Business fax,
Website and
Email address.

I have attached a few images of our panels and our brochure for reference.

The colours of the business card should feature our logo colours which are: RGB
Red 187
Green 207
Blue 65

Requirements
Must have
• Very modern fonts and design. Some of the designs shown especially the "Prisms" design which is a popular design.
Nice to have
• Creative but simple design. Very contemporary.
Should not have
• Anything ornate or old fashioned.

```html
<!DOCTYPE html>
<html lang="en">
<head>
<meta charset="utf-8">
<title>Ripplecraft Facades – Business Card</title>
<link href="https://fonts.googleapis.com/css2?family=Open+Sans:wght@400;600;700&display=swap" rel="stylesheet">
<style>
  :root{
    --backdrop:#2a2a2a;
    --card:#111112;
    --card-edge:#1c1c1e;
    --lime:#bbcf41;
    --silver:#a7a8aa;
    --white:#f2f2f2;
    --muted:#8a8b8d;
    --divider:#2b2b2d;
  }
  *{margin:0;padding:0;box-sizing:border-box}
  html,body{width:1200px;height:900px;overflow:hidden;background:var(--backdrop)}
  body{font-family:"Open Sans",Arial,sans-serif;position:relative}

  .card{
    position:absolute;top:314px;width:500px;height:286px;
    background:var(--card);border-radius:16px;
    box-shadow:0 10px 30px rgba(0,0,0,.45);overflow:hidden;
  }
  .card--front{left:70px}
  .card--back{left:630px}

  /* front */
  .front__divider{position:absolute;left:232px;top:0;bottom:0;width:1px;background:var(--divider)}
  .brand{position:absolute;left:34px;top:118px;display:flex;align-items:center;gap:10px}
  .brand__square{width:22px;height:22px;background:var(--lime)}
  .brand__name{font-weight:700;font-size:19px;color:var(--lime);letter-spacing:.2px;line-height:1.1}

  .details{position:absolute;left:258px;top:34px;color:var(--white)}
  .details__name{font-weight:700;font-size:17px;color:var(--lime);line-height:1.1}
  .details__role{font-size:12.5px;margin-top:2px}
  .details__address{font-size:12.5px;line-height:1.3;margin-top:22px}
  .contacts{list-style:none;margin-top:16px}
  .contacts li{display:flex;align-items:center;gap:9px;font-size:12.5px;line-height:1;height:18px}
  .contacts svg{width:11px;height:11px;flex:none;fill:var(--lime)}

  /* back */
  .back__texture{position:absolute;inset:0;
    background:radial-gradient(ellipse at 70% 30%,#1f1f21 0%,#131314 55%,#0e0e0f 100%)}
  .back__brand{position:absolute;left:120px;top:96px;display:flex;align-items:center;gap:12px}
  .back__brand .brand__square{width:28px;height:28px}
  .back__brand .brand__name{font-size:25px}
  .back__tagline{position:absolute;left:160px;top:140px;font-size:12px;letter-spacing:2px;color:var(--muted);line-height:1.3}
</style>
</head>
<body>

<section class="card card--front">
  <div class="front__divider"></div>
  <div class="brand">
    <span class="brand__square"></span>
    <span class="brand__name">Ripplecraft<br>Facades</span>
  </div>
  <div class="details">
    <p class="details__name">Marcus Hale</p>
    <p class="details__role">Managing Director</p>
    <p class="details__address">12345, Address Goes Here<br>Country Name, 123456</p>
    <ul class="contacts">
      <li><svg viewBox="0 0 12 12"><path d="M3 0h6a1 1 0 0 1 1 1v10a1 1 0 0 1-1 1H3a1 1 0 0 1-1-1V1a1 1 0 0 1 1-1zm0 1.5v8h6v-8z"/></svg>123-456-7890</li>
      <li><svg viewBox="0 0 12 12"><path d="M2.5 0.5l2 2.5-1.2 1.3a7 7 0 0 0 4.4 4.4L9 7.5l2.5 2-1.3 2C5 11.5.5 7 .5 1.8z"/></svg>(044)-456-7890</li>
      <li><svg viewBox="0 0 12 12"><path d="M3 0h5v3H3zM1 4h10v6H9v2H3v-2H1zm3 5v2h4V9z"/></svg>123-456-7890</li>
      <li><svg viewBox="0 0 12 12"><path d="M0 2h12v8H0zm1 1l5 4 5-4z"/></svg>info@ripplecraftmail.com</li>
      <li><svg viewBox="0 0 12 12"><circle cx="6" cy="6" r="6"/></svg>www.ripplecraftfacades.com</li>
    </ul>
  </div>
</section>

<section class="card card--back">
  <div class="back__texture" role="img" aria-label="Faint embossed prism panel pattern"></div>
  <div class="back__brand">
    <span class="brand__square"></span>
    <span class="brand__name">Ripplecraft Facades</span>
  </div>
  <p class="back__tagline">decorative panels for<br>interiors &amp; landscapes</p>
</section>

</body>
</html>
```